Business cards and stationary design

We just completed the design of our new logo and we need to print new business cards and letterhead for our nonprofit. We are looking for a fresh new design that shows off our new logo. On letterhead, we must have a column on the right or left to include our Board of Directors (up to 45 names) (see attachment)

Industry/Entity Type

Non-Profit

Contact Information for Business Card

Standard business card with name, title, Company name, mailing address phone numbers, email address and website. Tagline on back "Bringing the homeless home"

Font styles to use
Sans Serif

Requirements
Must have
• include pertinent information above
• new logo
• fonts compatible with logo
• should use logo colors only
Nice to have
• tag lines

```html
<!DOCTYPE html>
<html lang="en">
<head>
<meta charset="utf-8">
<title>Harbor Home Center — Business Card</title>
<link rel="stylesheet" href="https://fonts.googleapis.com/css2?family=Roboto:wght@400;500&family=Roboto+Condensed:wght@700&display=swap">
<style>
  :root {
    --teal: #0a7fa0;
    --teal-dark: #086d8a;
    --red: #d4202a;
    --paper: #f2f2f2;
    --ink: #4a4a4a;
    --rule: #c9c9c9;
    --backdrop: #2e2e2e;
    --white: #ffffff;
  }
  * { box-sizing: border-box; margin: 0; padding: 0; }
  html, body { width: 1200px; height: 960px; overflow: hidden; }
  body {
    background: var(--backdrop);
    font-family: "Roboto", Arial, sans-serif;
    position: relative;
  }
  .card {
    position: absolute;
    left: 320px;
    width: 600px;
    height: 342px;
    border-radius: 20px;
    overflow: hidden;
  }
  /* Back face */
  .card-back {
    top: 106px;
    background: var(--teal);
  }
  .card-back .brand-name {
    position: absolute;
    left: 0; right: 0; top: 236px;
    text-align: center;
    color: var(--white);
    font-family: "Roboto", Arial, sans-serif;
    font-weight: 500;
    font-size: 34px;
    letter-spacing: 3px;
  }
  .card-back .brand-dot {
    position: absolute;
    left: 270px; top: 120px;
    width: 60px; height: 60px;
    border-radius: 50%;
    background: var(--white);
  }
  .card-back .website {
    position: absolute;
    left: 0; right: 0; top: 294px;
    text-align: center;
    color: var(--white);
    font-size: 14px;
    letter-spacing: 5.2px;
  }
  /* Front face */
  .card-front {
    top: 493px;
    background: var(--paper);
  }
  .card-front .brand {
    position: absolute;
    right: 28px; top: 82px;
    display: flex; align-items: center; gap: 8px;
    color: var(--teal);
    font-family: "Roboto", Arial, sans-serif;
    font-weight: 500;
    font-size: 17px;
    letter-spacing: 2px;
  }
  .card-front .brand-mark {
    width: 12px; height: 12px; border-radius: 50%;
    background: var(--teal);
  }
  .person {
    position: absolute;
    left: 33px; top: 186px;
  }
  .person-name {
    font-family: "Roboto Condensed", Arial, sans-serif;
    font-weight: 700;
    font-size: 23px;
    color: var(--teal);
    line-height: 26px;
  }
  .person-title {
    font-family: "Roboto Condensed", Arial, sans-serif;
    font-weight: 700;
    font-size: 15px;
    color: var(--red);
    line-height: 20px;
  }
  .divider {
    position: absolute;
    left: 33px; right: 28px; top: 239px;
    border-top: 1px solid var(--rule);
  }
  .contact-list {
    position: absolute;
    left: 33px; top: 250px;
    list-style: none;
    font-size: 15px;
    color: var(--ink);
  }
  .contact-list li {
    display: flex; align-items: center; gap: 8px;
    height: 19px;
  }
  .contact-list svg { width: 14px; height: 14px; fill: var(--teal); }
  .address {
    position: absolute;
    right: 28px; top: 250px;
    text-align: right;
    font-size: 15px;
    line-height: 19px;
    color: var(--ink);
    font-style: normal;
  }
  .address .org { font-weight: 500; }
  .edge-line {
    position: absolute;
    left: 0; right: 0; top: 322px;
    height: 3px;
    background: var(--red);
  }
  .edge-band {
    position: absolute;
    left: 0; right: 0; top: 327px; bottom: 0;
    background: var(--teal);
  }
</style>
</head>
<body>

<section class="card card-back" aria-label="Card back">
  <div class="brand-dot"></div>
  <div class="brand-name">HARBOR HOME CENTER</div>
  <div class="website">www.harborhome.org</div>
</section>

<section class="card card-front" aria-label="Card front">
  <div class="brand"><span class="brand-mark"></span>HARBOR HOME CENTER</div>

  <div class="person">
    <div class="person-name">DANA WHITLOCK</div>
    <div class="person-title">CEO/FOUNDER</div>
  </div>

  <div class="divider"></div>

  <ul class="contact-list">
    <li>
      <svg viewBox="0 0 24 24" aria-hidden="true"><path d="M6.6 10.8a15.1 15.1 0 0 0 6.6 6.6l2.2-2.2c.3-.3.7-.4 1-.2 1.1.4 2.3.6 3.6.6.6 0 1 .4 1 1V20c0 .6-.4 1-1 1A17 17 0 0 1 3 4c0-.6.4-1 1-1h3.5c.6 0 1 .4 1 1 0 1.3.2 2.5.6 3.6.1.3 0 .7-.2 1z"/></svg>
      555 014 2290
    </li>
    <li>
      <svg viewBox="0 0 24 24" aria-hidden="true"><path d="M2 5h20v14H2z M4 7v.5l8 5 8-5V7l-8 5z" fill-rule="evenodd"/></svg>
      dana@harborhome.org
    </li>
    <li>
      <svg viewBox="0 0 24 24" aria-hidden="true"><path d="M12 2a10 10 0 1 0 0 20 10 10 0 0 0 0-20zm-1 17.9A8 8 0 0 1 4.1 11L9 16v1a2 2 0 0 0 2 2zm6.9-2.5A2 2 0 0 0 16 16h-1v-3a1 1 0 0 0-1-1H8v-2h2a1 1 0 0 0 1-1V7h2a2 2 0 0 0 2-2v-.4a8 8 0 0 1 2.9 12.8z"/></svg>
      www.harborhome.org
    </li>
  </ul>

  <address class="address">
    <div class="org">Harbor home center</div>
    <div>4120 Alder Court</div>
    <div>Fairbanks, Alaska 99712</div>
  </address>

  <div class="edge-line"></div>
  <div class="edge-band"></div>
</section>

</body>
</html>
```